Workshop PPT Update for AI Transformation Sessions

Our strategic consulting firm runs strategy workshops using slides as workshop exercises. These slides are used to communicate to the participants in advance, run the workshops and produce the final deliverable.

It is time for a design "upgrade". We'd like them to be more engaging, hipper and more interesting. These slides are utilitarian, so clean and usable is good. I have attached the example of what we have today. I have also attached an example of another company's slides that I like.

We can't rip off their design nor can we go away 100% from what we have. But I think it is possible to "update" our look to something closer to their look. Grey colors are fine with some color pop.

Slide styles needed are - 1) Cover Page, 2) Instructions Page, 3) Bullet list 4) Worksheet (place for participants to add content 5) Table, 6) Two column.

```html
<!DOCTYPE html>
<html lang="en">
<head>
<meta charset="utf-8">
<title>AI Transformation Workshop Slides</title>
<link href="https://fonts.googleapis.com/css2?family=Poppins:wght@300;400;700&family=Roboto:wght@400;500;700&display=swap" rel="stylesheet">
<style>
:root{
  --page:#fdf1f1;
  --dark:#3d3d3d;
  --red:#a83a3a;
  --red-soft:#fbeaea;
  --ink:#2b2b2b;
  --muted:#666;
  --white:#fff;
  --line:#d8d8d8;
}
*{margin:0;padding:0;box-sizing:border-box}
html,body{width:1200px;height:4051px;overflow:hidden}
body{background:var(--page);font-family:'Roboto',Arial,sans-serif;color:var(--ink);position:relative}
.slide{position:absolute;left:75px;width:1048px;height:588px;background:var(--white);overflow:hidden;box-shadow:0 4px 18px rgba(0,0,0,.12)}
.slide::after{content:"";position:absolute;right:0;top:0;width:420px;height:320px;background:radial-gradient(ellipse at top right,rgba(0,0,0,.05),rgba(0,0,0,0) 70%);pointer-events:none}
.accent{position:absolute;left:0;top:0;bottom:0;width:5px;background:var(--red);z-index:3}
.side{position:absolute;left:0;top:0;bottom:0;width:300px;background:var(--dark);color:var(--white)}
.title{position:absolute;left:60px;top:26px;font-family:'Poppins',sans-serif;font-size:37px;line-height:46px;color:var(--white)}
.title b{font-weight:700;display:block}
.title span{font-weight:300;display:block}
.brand{position:absolute;right:60px;top:26px;font-family:'Roboto',sans-serif;font-weight:500;font-size:28px;color:var(--dark);z-index:2}
.brand.light{color:var(--white)}
.pageno{position:absolute;left:951px;top:536px;width:36px;height:36px;border-radius:50%;border:3px solid var(--red);background:var(--white);font:700 13px 'Roboto',sans-serif;color:var(--ink);display:flex;align-items:center;justify-content:center;z-index:2}
/* steps */
.step{position:absolute;left:269px;display:flex;align-items:center}
.step .num{width:62px;height:62px;border-radius:50%;background:var(--red);border:5px solid var(--white);box-shadow:0 0 0 2px #e6e6e6;color:var(--white);font:700 22px 'Roboto',sans-serif;display:flex;align-items:center;justify-content:center}
.step p{margin-left:29px;font:700 17px 'Roboto',sans-serif;letter-spacing:.2px}
/* cover */
.cover{background:var(--dark)}
.photo-ring{position:absolute;left:60px;top:70px;width:450px;height:450px;border-radius:50%;background:var(--white);display:flex;align-items:center;justify-content:center}
.photo{width:426px;height:426px;border-radius:50%;background:radial-gradient(circle at 40% 40%,#8a7a6c,#3a3430 80%)}
.cover-head{position:absolute;left:550px;top:244px;color:var(--white);font-family:'Poppins',sans-serif;font-size:36px}
.cover-head b{font-weight:700}
.cover-head span{font-weight:300}
.cover-sub{position:absolute;left:550px;top:308px;color:var(--white);font:500 22px 'Roboto',sans-serif;letter-spacing:2.5px}
/* table */
.plan{position:absolute;left:373px;top:159px;width:617px;border-collapse:collapse;font-size:9px;text-align:center;box-shadow:0 2px 8px rgba(0,0,0,.15);z-index:2}
.plan th{background:var(--red);color:var(--white);font-weight:700;height:22px;font-size:8px;text-transform:uppercase}
.plan td{height:62px;border:1px solid var(--line);color:#444;line-height:1.6}
.plan tr:nth-child(even) td{background:#f1f1f1}
.plan .strong{font-weight:700}
.plan em{font-size:7.5px;display:block}
/* lists */
.section-head{position:absolute;left:360px;top:26px;font:700 19px 'Roboto',sans-serif;color:var(--red)}
.item{position:absolute;left:368px;display:flex;align-items:center}
.icon{width:50px;height:50px;border-radius:50%;background:var(--red-soft);display:flex;align-items:center;justify-content:center;flex:none}
.icon svg{width:26px;height:26px;fill:var(--red)}
.item .txt{margin-left:40px}
.item h3{font:700 14px 'Roboto',sans-serif;text-transform:uppercase}
.item p{font-size:11.5px;color:var(--muted);margin-top:6px}
.side-label{position:absolute;left:60px;font:700 13px 'Roboto',sans-serif;color:var(--white)}
.bullets{position:absolute;left:60px;list-style:none;font-size:10.5px;color:var(--white)}
.bullets li{position:relative;padding-left:24px;height:26px;font-weight:500}
.bullets li::before{content:"";position:absolute;left:0;top:2px;width:9px;height:9px;border-radius:50%;border:2px solid var(--red);background:#e66}
.pill{position:absolute;left:60px;width:152px;height:28px;border-radius:14px;font:700 9.5px 'Roboto',sans-serif;display:flex;align-items:center;justify-content:center;text-transform:uppercase}
.pill.red{background:var(--red);color:var(--white)}
.pill.white{background:var(--white);color:var(--ink)}
.footnote{position:absolute;left:360px;top:562px;font:500 10.5px 'Roboto',sans-serif;color:var(--ink)}
/* principles */
.principle{position:absolute;left:359px;width:620px}
.principle h3{font:700 17px 'Roboto',sans-serif;display:flex;align-items:center}
.principle h3 svg{width:17px;height:17px;margin-right:24px}
.principle p{margin:14px 0 0 41px;font-size:12px;line-height:20px;color:var(--muted)}
.side-q{position:absolute;left:60px;top:276px;width:220px;font:500 13.5px 'Roboto',sans-serif;line-height:22px;color:var(--white)}
</style>
</head>
<body>

<!-- Slide 1: Getting started -->
<section class="slide" style="top:88px">
  <div class="side"></div><div class="accent"></div>
  <h1 class="title"><b>Getting</b><span>Started</span></h1>
  <div class="brand">BrightPath</div>
  <div class="step" style="top:111px"><div class="num">1</div><p>COMPLETE THE ENGAGEMENT SIZING SURVEY.</p></div>
  <div class="step" style="top:213px"><div class="num">2</div><p>COLLECT RELEVANT INPUTS.</p></div>
  <div class="step" style="top:315px"><div class="num">3</div><p>DETERMINE WORKSHOP PARTICIPANTS &amp; DATE.</p></div>
  <div class="step" style="top:417px"><div class="num">4</div><p>SEND INVITES, TO INCLUDE PRE-WORK.</p></div>
  <div class="pageno">1</div>
</section>

<!-- Slide 2: Cover -->
<section class="slide cover" style="top:745px">
  <div class="accent"></div>
  <div class="brand light">BrightPath</div>
  <div class="photo-ring"><div class="photo" role="img" aria-label="Photo of a team gathered around a laptop in an office"></div></div>
  <h2 class="cover-head"><b>Kickoff &amp;</b> <span>Discovery</span></h2>
  <p class="cover-sub">Sizing &amp; Scoping AI Transformation</p>
  <div class="pageno">2</div>
</section>

<!-- Slide 3: Plan structure -->
<section class="slide" style="top:1403px">
  <div class="side"></div><div class="accent"></div>
  <h1 class="title"><b>Plan</b><span>Structure</span></h1>
  <div class="brand">BrightPath</div>
  <table class="plan">
    <colgroup><col style="width:40px"><col style="width:54px"><col style="width:239px"><col style="width:138px"><col style="width:146px"></colgroup>
    <tr><th colspan="2">Level</th><th>Planning Element &amp; Definition</th><th>Accountability/Owner</th><th>Frequency of Modification</th></tr>
    <tr><td>1</td><td>What<br>(overall)</td><td class="strong">Strategic Priorities</td><td>N/A</td><td>3+ years</td></tr>
    <tr><td>1.1</td><td>What<br>(this year)</td><td><span class="strong">Goals</span><em>Outcomes &amp; Strategies</em></td><td>Executive Leadership</td><td>1-3 years</td></tr>
    <tr><td>1.1.1</td><td rowspan="2">How</td><td class="strong">Key Performance Indicators<br>and/or Initiatives</td><td></td><td>1 year<br>(w/ qtly targets)</td></tr>
    <tr><td>1.1.1.1</td><td class="strong">Action Items</td><td></td><td>Quarterly/Monthly</td></tr>
  </table>
  <div class="pageno">3</div>
</section>

<!-- Slide 4: Workshop overview -->
<section class="slide" style="top:2060px">
  <div class="side"></div><div class="accent"></div>
  <h1 class="title"><b>Workshop</b><span>Overview</span></h1>
  <div class="side-label" style="top:229px">PREP WORK:</div>
  <ul class="bullets" style="top:263px">
    <li>Org Strategy</li><li>2023 Goal Performance</li><li>Existing policies</li><li>Pre-thinking questions</li>
  </ul>
  <div class="pill red" style="top:507px">Participants: Execs</div>
  <div class="pill white" style="top:544px">Duration: 2 hrs</div>
  <div class="brand">BrightPath</div>
  <h2 class="section-head">WORKSHOP FLOW</h2>
  <div class="item" style="top:79px"><div class="icon"><svg viewBox="0 0 24 24"><path d="M4 21V5h8v16H4zm2-13h1.5v1.5H6zm3 0h1.5v1.5H9zM6 11h1.5v1.5H6zm3 0h1.5v1.5H9zM6 14h1.5v1.5H6zm3 0h1.5v1.5H9zM13 21V9h7v12h-7z"/></svg></div><div class="txt"><h3>Confirm company direction</h3><p>Recap organizational purpose, values, vision &amp; winning strategy.</p></div></div>
  <div class="item" style="top:161px"><div class="icon"><svg viewBox="0 0 24 24"><path d="M10 3a7 7 0 0 0-5 11.9V21h7v-3h3v-4l2-.5-2-3.5A7 7 0 0 0 10 3z"/></svg></div><div class="txt"><h3>Develop AI vision</h3></div></div>
  <div class="item" style="top:239px"><div class="icon"><svg viewBox="0 0 24 24"><path d="M12 3l9 5-9 5-9-5zM3 12l9 5 9-5v3l-9 5-9-5z"/></svg></div><div class="txt"><h3>Develop AI guiding principles</h3><p>Developed AI Guiding Principles, supporting policies to include approved tools.</p></div></div>
  <div class="item" style="top:321px"><div class="icon"><svg viewBox="0 0 24 24"><path d="M11 3h2v8h6v-2l3 3-3 3v-2h-6v4h2l-3 3-3-3h2v-4H5v2l-3-3 3-3v2h6z"/></svg></div><div class="txt"><h3>Agree on a governance approach</h3><p>Agreed upon governance approach, structure, &amp; executive champion.</p></div></div>
  <div class="item" style="top:401px"><div class="icon"><svg viewBox="0 0 24 24"><circle cx="6" cy="7" r="2.5"/><path d="M3 21v-9h6v9zM10 4h11v11H10v-2h9V6h-9z"/></svg></div><div class="txt"><h3>Agree on a training &amp; learning approach</h3><p>Set approach to training &amp; continuous learning.</p></div></div>
  <div class="item" style="top:482px"><div class="icon"><svg viewBox="0 0 24 24"><path d="M3 4h14v10H8l-5 4zM19 8h2v12l-4-3h-7v-1h9z"/></svg></div><div class="txt"><h3>Determine rollout &amp; communication</h3><p>Organizational rollout &amp; continuous communication.</p></div></div>
  <p class="footnote">DELIVERABLES: Your Company's AI Playbook</p>
  <div class="pageno">4</div>
</section>

<!-- Slide 5: Instructions -->
<section class="slide" style="top:2718px">
  <div class="side"></div><div class="accent"></div>
  <h1 class="title" style="font-size:33px;line-height:42px"><b>Creating your</b><span>AI Guiding</span><span>Principles</span></h1>
  <div class="side-label" style="top:259px">YOUR EXISTING MATERIAL:</div>
  <ul class="bullets" style="top:292px">
    <li>Company Values</li><li>Current Policies (GDPR, CCPA, etc.)</li><li>Legal Guidance</li><li>OTHER</li>
  </ul>
  <div class="pill red" style="top:545px">PromptPal prompts: here</div>
  <div class="brand">BrightPath</div>
  <h2 class="section-head">INSTRUCTIONS:</h2>
  <div class="item" style="top:66px"><div class="icon"><svg viewBox="0 0 24 24"><path d="M5 2h10l4 4v9h-2V7h-3V4H7v16h6v2H5zM8 9h6v1.5H8zm0 3h6v1.5H8zm7 5l2 2 4-4 1 1-5 5-3-3z"/></svg></div><div class="txt"><h3>Create the outline.</h3><p>Determine the topics that need a principle.</p></div></div>
  <div class="item" style="top:148px"><div class="icon"><svg viewBox="0 0 24 24"><path d="M5 2h10l4 4v6h-2V7h-3V4H7v16h5v2H5zM8 9h6v1.5H8zm0 3h4v1.5H8z"/><circle cx="17" cy="17" r="3"/><path d="M19 19l3 3-1 1-3-3z"/></svg></div><div class="txt"><h3>Audit the outline.</h3><p>Look at the current policies to determine if all topics are covered.</p></div></div>
  <div class="item" style="top:241px"><div class="icon"><svg viewBox="0 0 24 24"><path d="M3 5h10v2H3zm0 4h8v2H3zm0 4h6v2H3zM18 4l3 3-9 9H9v-3z"/></svg></div><div class="txt"><h3>Draft the guiding principles.</h3></div></div>
  <div class="item" style="top:321px"><div class="icon"><svg viewBox="0 0 24 24"><path d="M12 2a6 6 0 0 0-6 6c0 4.5 6 11 6 11s6-6.5 6-11a6 6 0 0 0-6-6zm0 8.5A2.5 2.5 0 1 1 12 5.5a2.5 2.5 0 0 1 0 5zM5 20h14v2H5z"/></svg></div><div class="txt"><h3>Determine which GPs need detailed policies.</h3></div></div>
  <div class="item" style="top:403px"><div class="icon"><svg viewBox="0 0 24 24"><path d="M14 3l7 7-3 3-7-7zM10 7l7 7-6 6-7-7z"/></svg></div><div class="txt"><h3>Determine which AI tools support the GPs.</h3></div></div>
  <div class="item" style="top:483px"><div class="icon"><svg viewBox="0 0 24 24"><path d="M3 11h4v10H3zm6 10V11l4-7 2 1-1 5h6l-2 11z"/></svg></div><div class="txt"><h3>Finalize via a legal and executive review.</h3></div></div>
  <p class="footnote">PURPOSE: To create behavioral statements that everyone is expected to adhere to.</p>
  <div class="pageno">5</div>
</section>

<!-- Slide 6: Principles worksheet -->
<section class="slide" style="top:3375px">
  <div class="side"></div><div class="accent"></div>
  <h1 class="title" style="font-size:33px;line-height:42px"><b>AI Guiding</b><span>Principles</span></h1>
  <p class="side-q">What guides our decision-making and approach?</p>
  <div class="brand">BrightPath</div>
  <div class="principle" style="top:64px"><h3><svg viewBox="0 0 20 20"><circle cx="10" cy="10" r="10" fill="#a83a3a"/><path d="M5.5 10l3 3 6-6" stroke="#fff" stroke-width="2.2" fill="none"/></svg>PRINCIPLE #1</h3><p>Complete perspective from Executives, Directors, Managers &amp; Staff. Conduct competitive analysis and customer research (optional)</p></div>
  <div class="principle" style="top:160px"><h3><svg viewBox="0 0 20 20"><circle cx="10" cy="10" r="10" fill="#a83a3a"/><path d="M5.5 10l3 3 6-6" stroke="#fff" stroke-width="2.2" fill="none"/></svg>PRINCIPLE #2</h3><p>Complete perspective from Executives, Directors, Managers &amp; Staff. Conduct competitive analysis and customer research (optional)</p></div>
  <div class="principle" style="top:257px"><h3><svg viewBox="0 0 20 20"><circle cx="10" cy="10" r="10" fill="#a83a3a"/><path d="M5.5 10l3 3 6-6" stroke="#fff" stroke-width="2.2" fill="none"/></svg>PRINCIPLE #3</h3><p>Complete perspective from Executives, Directors, Managers &amp; Staff. Conduct competitive analysis and customer research (optional).</p></div>
  <div class="principle" style="top:353px"><h3><svg viewBox="0 0 20 20"><circle cx="10" cy="10" r="10" fill="#a83a3a"/><path d="M5.5 10l3 3 6-6" stroke="#fff" stroke-width="2.2" fill="none"/></svg>PRINCIPLE #4</h3><p>Complete perspective from Executives, Directors, Managers &amp; Staff. Conduct competitive analysis and customer research (optional).</p></div>
  <div class="principle" style="top:449px"><h3><svg viewBox="0 0 20 20"><circle cx="10" cy="10" r="10" fill="#a83a3a"/><path d="M5.5 10l3 3 6-6" stroke="#fff" stroke-width="2.2" fill="none"/></svg>PRINCIPLE #5</h3><p>Complete perspective from Executives, Directors, Managers &amp; Staff. Conduct competitive analysis and customer research (optional).</p></div>
  <div class="pageno">6</div>
</section>

</body>
</html>
```